Modern Business Card For A Digital Advertising Company

I'll be print on the Pell Prints Velour paper http://us.pellprints.com/products/velour/business-cards.html
Need's to be modern and use the color palette of the logo or gray scales. I think integrating the pixelation of the logo in to the card and having it wrap from one side to the other could be interesting. My company provides ad operations, web development, and number of other services to websites around the world. You can see my website at http://www.zantorhq.com
Contact info on the card needs to have
Owen Lasko
President
p.318.204.6637
owen@zantorhq.com
http://www.zantorhq.com
Doesn't necessarily need to be in that order
Website owners
Business

```html
<!DOCTYPE html>
<html lang="en">
<head>
<meta charset="utf-8">
<title>Zantor HQ – Business Card</title>
<link rel="stylesheet" href="https://fonts.googleapis.com/css2?family=Open+Sans:wght@400;700&display=swap">
<style>
  :root {
    --stage: #000000;
    --card: #ffffff;
    --green-deep: #7aaa1f;
    --green-light: #a9cc2c;
    --brand-green: #8dc63f;
    --name-green: #0b8a3c;
    --icon-green: #149a45;
    --ink: #111111;
  }
  * { margin: 0; padding: 0; box-sizing: border-box; }
  html, body {
    width: 900px; height: 1200px; overflow: hidden;
    background: var(--stage);
    font-family: "Open Sans", Tahoma, sans-serif;
  }
  .canvas { position: relative; width: 900px; height: 1200px; }
  .card {
    position: absolute; width: 758px; height: 466px;
    background: var(--card); overflow: hidden;
  }
  .card--front { left: 70px; top: 87px; }
  .card--back { left: 69px; top: 623px; }
  .card__panel { position: absolute; inset: 0; width: 100%; height: 100%; }

  .brand {
    position: absolute; left: 86px; top: 262px;
    display: flex; align-items: center; gap: 16px;
  }
  .brand__mark { width: 34px; height: 34px; background: var(--brand-green); }
  .brand__name {
    font-size: 50px; font-weight: 700; color: var(--brand-green);
    letter-spacing: 1px; line-height: 1;
  }

  .identity { position: absolute; right: 42px; top: 52px; text-align: right; }
  .identity__name { font-size: 31px; font-weight: 700; color: var(--name-green); line-height: 1.2; }
  .identity__title { font-size: 23px; color: var(--ink); line-height: 1.4; }

  .contacts { position: absolute; left: 387px; top: 261px; list-style: none; }
  .contacts__item {
    display: flex; align-items: center; gap: 16px;
    font-size: 23px; color: var(--ink); height: 39px; letter-spacing: 0.4px;
  }
  .contacts__icon { width: 24px; height: 24px; flex: none; }
</style>
</head>
<body>
<main class="canvas">

  <section class="card card--front">
    <svg class="card__panel" viewBox="0 0 758 466" preserveAspectRatio="none" role="img" aria-label="Decorative green gradient panel">
      <defs>
        <linearGradient id="front-fill" x1="0" y1="1" x2="1" y2="0">
          <stop offset="0" stop-color="var(--green-light)"/>
          <stop offset="1" stop-color="var(--green-deep)"/>
        </linearGradient>
      </defs>
      <path d="M348 466 Q560 260 570 0 L758 0 L758 466 Z" fill="url(#front-fill)"/>
    </svg>
    <div class="brand">
      <span class="brand__mark"></span>
      <span class="brand__name">Zantor HQ</span>
    </div>
  </section>

  <section class="card card--back">
    <svg class="card__panel" viewBox="0 0 758 466" preserveAspectRatio="none" role="img" aria-label="Decorative green gradient panel">
      <defs>
        <linearGradient id="back-fill" x1="1" y1="1" x2="0" y2="0">
          <stop offset="0" stop-color="var(--green-light)"/>
          <stop offset="1" stop-color="var(--green-deep)"/>
        </linearGradient>
      </defs>
      <path d="M188 0 Q230 330 406 466 L0 466 L0 0 Z" fill="url(#back-fill)"/>
    </svg>

    <div class="identity">
      <p class="identity__name">Owen Lasko</p>
      <p class="identity__title">President</p>
    </div>

    <ul class="contacts">
      <li class="contacts__item">
        <svg class="contacts__icon" viewBox="0 0 24 24" aria-hidden="true">
          <circle cx="12" cy="12" r="10.5" fill="none" stroke="var(--icon-green)" stroke-width="1.5"/>
          <path d="M9 6.5 L10.8 9.5 L9.8 10.8 C10.5 12.5 11.6 13.7 13.3 14.4 L14.6 13.4 L17.5 15.2 L16.5 17.3 C11.5 17 7.5 12.8 7.2 8 Z" fill="var(--icon-green)"/>
        </svg>
        <span>318-204-6637</span>
      </li>
      <li class="contacts__item">
        <svg class="contacts__icon" viewBox="0 0 24 24" aria-hidden="true">
          <rect x="2" y="6" width="20" height="13" fill="none" stroke="var(--icon-green)" stroke-width="1.5"/>
          <path d="M2 6 L12 14 L22 6 M2 19 L9.5 12 M22 19 L14.5 12" fill="none" stroke="var(--icon-green)" stroke-width="1.5"/>
        </svg>
        <span>owen@zantorhq.com</span>
      </li>
      <li class="contacts__item">
        <svg class="contacts__icon" viewBox="0 0 24 24" aria-hidden="true">
          <circle cx="12" cy="12" r="10.5" fill="var(--icon-green)"/>
          <g fill="none" stroke="#ffffff" stroke-width="1.2">
            <ellipse cx="12" cy="12" rx="4.5" ry="10.5"/>
            <path d="M1.5 12 H22.5 M3 7 H21 M3 17 H21 M12 1.5 V22.5"/>
          </g>
        </svg>
        <span>www.zantorhq.com</span>
      </li>
    </ul>
  </section>

</main>
</body>
</html>
```